Business card design for Virtual Assistance company

I need a business card designed for my virtual assistance company. We are a small company who services primarily C-level executive clients. The card needs to be double sided with the following contact information on the back:
Melissa Thornbury
Owner/CEO
info@rkpadvisory.net
www.rkpadvisory.net
555.302.9817

The front side should just have the company name incorporated: "RKP Advisory" and "virtual assistance"

The card should be simplistic, but eye catching and should speak to high level executives. Our primary focus areas consist of executive assistance and government contracting.

Target Market(s)

CEOs and executives

Contact Information for Business Card

see project description. phone, email, website.

Colors

Designer to choose only greyscale colors for use in the design.

```html
<!DOCTYPE html>
<html lang="en">
<head>
<meta charset="utf-8">
<title>RKP Advisory – Business Card</title>
<link href="https://fonts.googleapis.com/css2?family=Cinzel:wght@500;600&family=Poppins:wght@400&family=Archivo+Black&display=swap" rel="stylesheet">
<style>
  :root{
    --stage:#2b2b2b;
    --card:#161616;
    --card-edge:#1d1d1d;
    --silver:#c9c9c9;
    --band:#d4d4d4;
    --white:#f4f4f4;
    --emboss:#3a3a3a;
    --emboss-line:#444;
    --rule:#5a5a5a;
    --ink:#111;
  }
  *{box-sizing:border-box;margin:0;padding:0}
  html,body{width:1200px;height:689px;overflow:hidden;background:var(--stage)}
  .stage{position:relative;width:1200px;height:689px;display:flex;align-items:center;justify-content:center;gap:44px}
  .card{position:relative;width:540px;height:309px;border-radius:18px;background:var(--card);overflow:hidden;box-shadow:0 0 0 1px var(--card-edge)}

  /* Front */
  .front{display:flex;flex-direction:column;align-items:center;justify-content:center}
  .front .brand{font-family:"Cinzel",serif;font-weight:600;font-size:58px;letter-spacing:4px;color:var(--emboss);text-transform:uppercase;white-space:nowrap}
  .front .tagline{display:flex;align-items:center;gap:14px;margin-top:10px;font-family:"Cinzel",serif;font-weight:500;font-size:17px;letter-spacing:6px;color:var(--emboss)}
  .front .tagline::before,.front .tagline::after{content:"";width:46px;height:2px;background:var(--emboss-line)}

  /* Back */
  .back .brand{position:absolute;left:30px;top:112px;width:230px;text-align:center;font-family:"Cinzel",serif;font-weight:600;font-size:34px;letter-spacing:2px;line-height:1.15;color:var(--white);text-transform:uppercase}
  .back .divider{position:absolute;left:286px;top:40px;width:1px;height:170px;background:var(--rule)}
  .back .details{position:absolute;left:310px;top:44px;right:18px}
  .back .name{font-family:"Cinzel",serif;font-weight:500;font-size:19px;color:var(--silver);text-transform:uppercase;letter-spacing:.5px;white-space:nowrap}
  .back .role{font-family:"Poppins",sans-serif;font-size:14px;color:var(--white);margin-top:2px}
  .back .contacts{list-style:none;margin-top:24px}
  .back .contacts li{display:flex;align-items:center;gap:9px;font-family:"Poppins",sans-serif;font-size:13.5px;color:var(--white);line-height:1.6}
  .back .contacts svg{width:13px;height:13px;flex:none}
  .back .band-rule{position:absolute;left:0;right:0;bottom:62px;height:1px;background:var(--rule)}
  .back .band{position:absolute;left:0;right:0;bottom:0;height:54px;background:var(--band);display:flex;align-items:center;justify-content:center;font-family:"Archivo Black",sans-serif;font-size:22px;letter-spacing:2px;color:var(--ink);text-transform:uppercase}
</style>
</head>
<body>
<main class="stage">
  <section class="card front" aria-label="Card front">
    <h1 class="brand">RKP Advisory</h1>
    <p class="tagline">VIRTUAL ASSISTANCE</p>
  </section>

  <section class="card back" aria-label="Card back">
    <p class="brand">RKP Advisory</p>
    <div class="divider"></div>
    <div class="details">
      <p class="name">Melissa Thornbury</p>
      <p class="role">Owner/CEO</p>
      <ul class="contacts">
        <li>
          <svg viewBox="0 0 16 16" aria-hidden="true"><path fill="var(--silver)" d="M3.6 1.5l2.2 2.6-1.3 1.6c.9 2 2.5 3.6 4.5 4.5l1.6-1.3 2.6 2.2-1.4 2.4C6.9 13.3 2.7 9.1 1.2 2.9z"/></svg>
          555.302.9817
        </li>
        <li>
          <svg viewBox="0 0 16 16" aria-hidden="true"><rect x="1" y="3" width="14" height="10" fill="var(--silver)"/><path d="M1 3l7 6 7-6" fill="none" stroke="var(--card)" stroke-width="1.4"/></svg>
          info@rkpadvisory.net
        </li>
        <li>
          <svg viewBox="0 0 16 16" aria-hidden="true"><g fill="none" stroke="var(--silver)" stroke-width="1.5"><circle cx="8" cy="8" r="6.5"/><ellipse cx="8" cy="8" rx="3" ry="6.5"/><path d="M1.5 8h13M3 4.5h10M3 11.5h10"/></g></svg>
          www.rkpadvisory.net
        </li>
      </ul>
    </div>
    <div class="band-rule"></div>
    <p class="band">Virtual Assistance</p>
  </section>
</main>
</body>
</html>
```